indépendant en tant que Massothérapeute et Préparateur Mental, j'ai besoin de ...

Massothérapeute et préparateur mental indépendant, je recherche une carte de visite sobre et dynamique, sans images liées au massage ou à la préparation mentale mais intégrant mon logo. Les couleurs que j'aime bien sont : Blanc, gris, anthracite, noir et jaune

Contact Information for Business Card

carte de préférence Horizontale
neutre qui puisse toucher le deux domaines Massothérapie et préparation mentale

Requirements
Must have
• mon projet doit intégrer au recto:
LOGO
Loïc Bardèze
078 513 26 48
info@loicbardeze.ch
et éventuellement www.loicbardeze.ch

et au verso les deux adresses:

Chemin des Ormilles 7B
1400 Yverdon-les-Bains

Route de la Gravière 9
1700 Fribourg

Should not have
• mon projet ne doit pas contenir d'image en liens avec le massage ni la préparation mentale.

```html
<!DOCTYPE html>
<html lang="fr">
<head>
<meta charset="utf-8">
<title>Loïc Bardèze – Carte de visite</title>
<link rel="stylesheet" href="https://fonts.googleapis.com/css2?family=Exo+2:wght@400;600;700&display=swap">
<style>
  :root {
    --page-bg: #d9d6d2;
    --anthracite: #1d1d1f;
    --anthracite-light: #3a3a3c;
    --frost-light: #eceae8;
    --frost-mid: #cfccc8;
    --silver: #e8e8ea;
    --text-light: #dcdcdc;
    --text-strong: #f4f4f4;
    --ink: #141414;
  }
  * { margin: 0; padding: 0; box-sizing: border-box; }
  html, body {
    width: 1200px; height: 969px; overflow: hidden;
    background: var(--page-bg);
    font-family: "Exo 2", sans-serif;
  }
  .card {
    position: absolute; left: 100px; top: 200px;
    width: 1000px; height: 568px;
    border-radius: 26px; overflow: hidden;
    box-shadow: 0 18px 40px rgba(0,0,0,.22);
  }
  .card-shapes { position: absolute; inset: 0; }
  .contact {
    position: absolute; left: 52px; top: 122px;
    color: var(--text-light);
  }
  .contact-name {
    font-size: 30px; font-weight: 400; color: var(--text-strong);
    letter-spacing: .5px; margin-bottom: 34px;
  }
  .contact-name strong { font-weight: 700; }
  .address { font-size: 20px; line-height: 28px; margin-bottom: 6px; }
  .contact-list { list-style: none; margin-top: 22px; font-size: 20px; }
  .contact-list li { display: flex; align-items: center; height: 29px; }
  .contact-list svg { width: 17px; height: 17px; margin-right: 14px; fill: var(--text-light); }
  .brand {
    position: absolute; left: 475px; top: 262px;
    display: flex; align-items: center; gap: 14px; color: var(--ink);
  }
  .brand-mark { width: 34px; height: 34px; background: var(--ink); }
  .brand-name { font-size: 30px; font-weight: 700; line-height: 1; letter-spacing: .5px; }
  .brand-role { font-size: 12.5px; font-weight: 700; margin-top: 5px; letter-spacing: .3px; }
</style>
</head>
<body>
<div class="card">
  <svg class="card-shapes" viewBox="0 0 1000 568" width="1000" height="568">
    <defs>
      <linearGradient id="frost" x1="0" y1="0" x2="1" y2="1">
        <stop offset="0" stop-color="var(--frost-light)"/>
        <stop offset="1" stop-color="var(--frost-mid)"/>
      </linearGradient>
      <linearGradient id="dark" x1="0" y1="0" x2="0.6" y2="1">
        <stop offset="0" stop-color="var(--anthracite-light)"/>
        <stop offset="1" stop-color="var(--anthracite)"/>
      </linearGradient>
    </defs>
    <rect class="frost-panel" width="1000" height="568" fill="url(#frost)"/>
    <path class="dark-panel" d="M0 0 H634 L398 222 Q370 250 396 284 L588 568 H0 Z" fill="url(#dark)"/>
    <path class="silver-rule" d="M648 0 L414 222 Q388 250 412 284 L602 568" fill="none" stroke="var(--silver)" stroke-width="3"/>
  </svg>

  <div class="contact">
    <p class="contact-name">Loïc <strong>BARDÈZE</strong></p>
    <p class="address">Chemin des Ormilles 7B<br>1400 Yverdon-les-Bain</p>
    <p class="address">Route de la Gravière 9<br>1700 Fribourg</p>
    <ul class="contact-list">
      <li><svg viewBox="0 0 24 24"><path d="M6.6 10.8a15 15 0 0 0 6.6 6.6l2.2-2.2a1 1 0 0 1 1-.25 11.4 11.4 0 0 0 3.6.57 1 1 0 0 1 1 1V20a1 1 0 0 1-1 1A17 17 0 0 1 3 4a1 1 0 0 1 1-1h3.5a1 1 0 0 1 1 1c0 1.25.2 2.45.57 3.57a1 1 0 0 1-.25 1z"/></svg>078 513 26 48</li>
      <li><svg viewBox="0 0 24 24"><path d="M2 5h20v14H2z M2 5l10 8 10-8" stroke="#1d1d1f" stroke-width="1.6"/></svg>info@loicbardeze.ch</li>
      <li><svg viewBox="0 0 24 24"><circle cx="12" cy="12" r="10"/></svg>www.loicbardeze.ch</li>
    </ul>
  </div>

  <div class="brand">
    <span class="brand-mark"></span>
    <div>
      <p class="brand-name">Loïc BARDÈZE</p>
      <p class="brand-role">MASSOTHÉRAPEUTE / PRÉPARATEUR MENTAL</p>
    </div>
  </div>
</div>
</body>
</html>
```